Soap Company Looking To Design New Soap Scent Boxes

we are looking to create a soap box similar to vel korrin. we would like the circle cut out on the top right corner of the box. we are looking for a design that will allow us to use different color base banners for different soap scents (like vel. korrin). we want the soap name scents to be large and readable on the bottom banner (like vel.korrin). we have included our brand figure (logo) and some previous older soap box designs that we were making before the brand figure. the box dims are attached.

```html
<!DOCTYPE html>
<html lang="en">
<head>
<meta charset="utf-8">
<title>Fenwick Glen – Plumeria Soap Box</title>
<link href="https://fonts.googleapis.com/css2?family=Kanit:wght@400;500;600;700&family=Lato:wght@400;700&display=swap" rel="stylesheet">
<style>
  :root {
    --kraft: #d6c4aa;
    --kraft-dark: #c9b699;
    --banner: #7a1519;
    --dieline: #d3343a;
    --ink: #3a2418;
    --white: #ffffff;
    --leaf: #2f8a4a;
  }
  * { margin: 0; padding: 0; box-sizing: border-box; }
  html, body { width: 1200px; height: 1110px; overflow: hidden; background: var(--kraft); }
  .box {
    position: relative;
    width: 1200px; height: 1110px;
    background: linear-gradient(180deg, var(--kraft) 0%, var(--kraft-dark) 100%);
    font-family: "Kanit", sans-serif;
    overflow: hidden;
  }
  .art { position: absolute; inset: 0; }

  .scent-list {
    position: absolute; right: 1094px; top: 204px;
    font-family: "Lato", sans-serif; color: var(--banner);
    font-size: 16.5px; line-height: 22.8px; text-align: right; white-space: nowrap;
  }
  .scent-list h3 {
    background: var(--banner); color: var(--white);
    font-size: 13px; letter-spacing: 0.5px; font-weight: 700;
    padding: 2px 6px; margin-bottom: 8px; text-transform: uppercase;
    display: inline-block;
  }
  .side-name {
    position: absolute; right: 1117px; top: 752px; white-space: nowrap;
    color: var(--white); font-size: 21px; font-weight: 500; letter-spacing: 1px;
  }

  .brand-name {
    position: absolute; left: 210px; top: 470px; width: 600px; text-align: center;
    font-size: 84px; font-weight: 700; line-height: 1; color: var(--ink);
  }

  .product {
    position: absolute; left: 173px; width: 856px; top: 764px;
    text-align: center; color: var(--white);
  }
  .product-kind { font-size: 35px; font-weight: 400; letter-spacing: 1px; line-height: 1.1; }
  .product-scent { font-size: 92px; font-weight: 700; letter-spacing: 2px; line-height: 1; margin-top: 2px; }
  .product-meta { margin-top: 16px; font-size: 23px; font-weight: 600; }
  .product-meta .tag {
    background: var(--white); color: var(--banner);
    padding: 0 6px; border-radius: 3px;
  }

  .tagline {
    position: absolute; left: 1060px; top: 360px; width: 220px;
    text-align: center; color: var(--leaf);
    font-size: 21px; font-weight: 500; letter-spacing: 2px; line-height: 1.3;
  }
</style>
</head>
<body>
<main class="box">
  <svg class="art" width="1200" height="1110" viewBox="0 0 1200 1110">
    <rect class="banner-side" x="0" y="688" width="173" height="422" fill="var(--banner)"/>
    <path class="banner-front" d="M173 715 C 420 725, 700 700, 1029 545 L1029 1110 L173 1110 Z" fill="var(--banner)"/>
    <rect class="banner-side" x="1029" y="541" width="171" height="569" fill="var(--banner)"/>

    <circle class="window-ring" cx="741" cy="304" r="101" fill="var(--white)"/>
    <circle class="window" cx="741" cy="304" r="89" fill="var(--banner)"/>

    <g class="dieline" stroke="var(--dieline)" stroke-width="1.5" fill="none">
      <line x1="173" y1="0" x2="173" y2="1110"/>
      <line x1="1029" y1="0" x2="1029" y2="1110"/>
      <line x1="0" y1="141" x2="1200" y2="141"/>
      <line x1="0" y1="992" x2="1200" y2="992"/>
      <path d="M144 0 L173 70 L173 141"/>
      <path d="M1058 0 L1029 70"/>
    </g>

    <circle class="flower-mark" cx="32" cy="840" r="32" fill="var(--white)" opacity="0.9" role="img" aria-label="Plumeria flower icon"/>
    <rect class="lotus-mark" x="1120" y="230" width="90" height="70" rx="35" fill="var(--leaf)" opacity="0.35" role="img" aria-label="Lotus outline ornament"/>

    <g class="eco-icons" fill="none" stroke="var(--white)" stroke-width="4">
      <circle cx="1121" cy="930" r="18"/>
      <path d="M1121 914 l8 10 h-16 z" fill="var(--white)" stroke="none"/>
      <rect x="1160" y="912" width="34" height="34" rx="6"/>
    </g>
  </svg>

  <aside class="scent-list">
    <h3>Available Scents</h3>
    <div>Sandalwood Tea Tree</div>
    <div>Charcoal Aloe</div>
    <div>Rose Floral Water</div>
    <div>Dead Sea Scrub</div>
    <div>Eucalyptus Aloe</div>
    <div>Hydrangea</div>
    <div>Cilantro Lime Scrub</div>
    <div>Mango Papaya</div>
    <div>Mountain Air</div>
    <div>Nag Champa</div>
    <div>Plumeria</div>
    <div>Pomegranate Cherry</div>
    <div>Raspberry Rush</div>
    <div>Strawberry Vanilla</div>
    <div>Sandalwood Rose</div>
    <div>Sunshine Grapefruit</div>
    <div>Wild Passion</div>
    <div>Wildflowers</div>
  </aside>

  <div class="side-name">PLUMERIA</div>

  <header class="brand-name">Fenwick Glen</header>

  <section class="product">
    <p class="product-kind">NATURAL SOAP</p>
    <h1 class="product-scent">PLUMERIA</h1>
    <p class="product-meta">COLD PRESSED <span class="tag">ARTISAN SOAP</span> Net Wt. 5Oz / 140g</p>
  </section>

  <p class="tagline">REJUVENATE<br>YOUR MIND<br>BODY &amp;<br>SOUL</p>
</main>
</body>
</html>
```